Etikett für Rotweinflasche
Liebe farbkosmos Atelier, wir werden uns bei der endgültigen Etikettengestaltung (finale Größe + Rückseite) noch an Euch melden. Bitte sendet uns euren Kontakt an helga.brandt@morvelli.wine
Zielgruppe
Morvelli Italia ist ein exklusives Boutique-Weingut in Sizilien, das hochqualitative Spitzenweine in kleinen Mengen mit modernster Technologie und stets nachhaltig erzeugt. Wir hinterfragen sowohl in der Agronomie im Weingarten als auch in der Önologie im Weinkeller alle herrschenden Traditionen und trachten danach, stets das beste Endprodukt zu kreieren. Der vulkanische, kalkreiche Boden Siziliens sowie trockene, sonnenreiche und niederschlagsarme Vegetationsperioden sind unsere optimale Basis.
Zielgruppe: Internationale Genussmenschen jeglichen Alters, die sich bewusst auch höherpreisige Weine (um die €30+) gönnen , vor allem kunstaffine young professionals mit Qualitäts-& Nachhaltigkeitsanspruch
Aufgabenstellung
Das Etikett ist für Rotwein-Flaschen (Cabernet Sauvignon / Nero D'Avola / Frappato / Syrah / Cerasuolo / Petit Verdot / sowie einen Bourdeaux-Cuveè aus Cabernet Sauvignon und Petit Verdot) .
Die Flasche ist reinschwarz, sehr hochwertig und schwer.
Flaschenform: Bordeauxflasche siehe technisches Datenblatt
Sleeve über dem Korken: schwarz mit weißer Schrift wie bisher
Zu gestalten ist das Etikett der Vorderseite. Zumindest die jeweilige Rotwein-Sorte ist auch textlich darzustellen (zwecks Scannen mit Trubel-App)
Der Kreativität kann freien Lauf gelassen werden! Unterscheidbarkeit vom Markt ist explizit gewollt.
Unsere aktuellen Etiketten und Markenauftritt siehe: https://morvelli.wine/shop/

```html
<!DOCTYPE html>
<html lang="de">
<head>
<meta charset="utf-8">
<title>Morvelli – Cabernet Sauvignon Etikett</title>
<link rel="stylesheet" href="https://fonts.googleapis.com/css2?family=EB+Garamond:wght@400;500&display=swap">
<style>
  :root {
    --canvas-bg: #ffffff;
    --label-deep: #2a2430;
    --label-teal: #3f7f95;
    --label-mist: #9fc3d2;
    --label-rose: #d9646a;
    --label-berry: #7a3a4a;
    --label-text: #f4f1ee;
  }
  * { margin: 0; padding: 0; box-sizing: border-box; }
  html, body {
    width: 849px;
    height: 1200px;
    overflow: hidden;
    background: var(--canvas-bg);
  }
  .canvas {
    position: relative;
    width: 849px;
    height: 1200px;
    display: flex;
    align-items: center;
    justify-content: center;
  }
  .front-label {
    position: relative;
    width: 760px;
    height: 456px;
    overflow: hidden;
    background: var(--label-deep);
  }
  .label-artwork {
    position: absolute;
    inset: 0;
    background:
      radial-gradient(ellipse 22% 40% at 50% 62%, var(--label-rose) 0%, rgba(217,100,106,0.55) 45%, rgba(217,100,106,0) 100%),
      radial-gradient(ellipse 40% 35% at 52% 30%, var(--label-mist) 0%, rgba(159,195,210,0) 100%),
      radial-gradient(ellipse 30% 45% at 8% 55%, var(--label-teal) 0%, rgba(63,127,149,0) 100%),
      radial-gradient(ellipse 35% 40% at 20% 10%, var(--label-berry) 0%, rgba(122,58,74,0) 100%),
      linear-gradient(180deg, #4c5f72 0%, #4a4150 55%, var(--label-deep) 100%);
  }
  .variety-name {
    position: absolute;
    left: 0;
    right: 0;
    bottom: 34px;
    text-align: center;
    font-family: "EB Garamond", Georgia, serif;
    font-weight: 400;
    font-size: 27px;
    letter-spacing: 0.16em;
    color: var(--label-text);
    text-transform: uppercase;
  }
</style>
</head>
<body>
  <main class="canvas">
    <section class="front-label">
      <div class="label-artwork" role="img" aria-label="Fotografie: Frau in wallendem rosaroten Kleid in einem verwunschenen Wald mit bläulichen Bäumen und roten Blättern"></div>
      <p class="variety-name">Cabernet Sauvignon</p>
    </section>
  </main>
</body>
</html>
```